Foot and ankle surgeon requires a website design

I need a website where prospective and established patients can obtain information and then direct them to making appointments. My practice is a highly professional surgical practice specialising in surgery to the foot and ankle. My title is Mr Colin Brasket, Podiatric Foot & Ankle Surgeon. My qualifications are: BSc MSc FACPS
The practice website will require information on: Locations, phone numbers to make appointments, general background on podiatric surgery,
I would like to include information on: my hospital appointments, surgical fellowships held, training programs undertaken, association memberships, publications written, links to useful websites
A page dedicated to common foot conditions would be useful and also a page with referral information including an online registration section that will be sent direct to the receptionist.
Examples of similar websites include:
http://www.dorvelquintaro.com.au/
http://www.haldenfootsurgeon.com.au/
I will provide files on logo, self photos and my personal training history etc.
Also if there is going to be a background theme I personally am associated with surfing and beach activities, it would be great if this was able to be reflected in the design.
Thank you.

```html
<!DOCTYPE html>
<html lang="en">
<head>
<meta charset="utf-8">
<title>Mr Colin Brasket – Podiatric Foot &amp; Ankle Surgeon</title>
<link rel="stylesheet" href="https://fonts.googleapis.com/css2?family=Ubuntu:wght@400;500;700&family=Rubik:wght@700&family=Dancing+Script:wght@500&family=Open+Sans:wght@400;600;700&display=swap">
<style>
:root{
  --navy:#0f3e73;
  --navy-dark:#0b3462;
  --orange:#e8760a;
  --orange-dark:#d4660a;
  --grey-text:#8a8a8a;
  --light-grey:#e6e6e6;
  --page:#f2f2f2;
  --white:#ffffff;
  --ink:#444;
}
*{margin:0;padding:0;box-sizing:border-box}
html,body{width:682px;height:1200px;overflow:hidden}
body{background:var(--page);font-family:"Open Sans",Arial,sans-serif;color:var(--ink);position:relative}
.container{position:absolute;left:50px;width:582px}

/* header */
.header{top:0;height:94px;background:linear-gradient(180deg,#fff 0%,#fbf7ef 100%);left:50px;width:582px;position:absolute}
.brand{position:absolute;left:22px;top:34px;display:flex;align-items:center;gap:8px}
.brand-dot{width:20px;height:20px;border-radius:50%;background:var(--orange)}
.brand-name{font-family:"Ubuntu",sans-serif;font-weight:500;font-size:15px;color:var(--navy)}
.contact-top{position:absolute;right:25px;top:9px;text-align:right;font-size:7.5px;line-height:13px;color:#555}
.contact-top .phone{font-size:10px;font-weight:700;color:var(--navy)}
.socials{position:absolute;right:25px;top:68px;display:flex;gap:3px}
.socials span{width:18px;height:18px;border-radius:50%;background:var(--navy)}
.socials span:nth-child(2){background:var(--orange)}
.socials span:nth-child(3){background:#3aaee0}
.socials span:nth-child(4){background:#1a5d9a}
.socials span:nth-child(5){background:#2d4f6e}

/* nav */
.nav{top:94px;height:33px;background:var(--orange);display:flex;align-items:center;padding-left:25px}
.nav a{color:#fff;text-decoration:none;font-size:8px;padding:0 8.5px;height:33px;line-height:33px}
.nav a.active{background:var(--orange-dark)}

/* hero */
.hero-band{position:absolute;left:0;top:127px;width:682px;height:292px;background:var(--navy)}
.hero{top:127px;height:292px;overflow:hidden}
.hero-photo{position:absolute;inset:0;background:linear-gradient(120deg,#e9ddd4 0%,#d9b9a6 35%,#f1ebe6 60%,#cfd8cf 100%)}
.hero-script{position:absolute;left:26px;top:203px;font-family:"Dancing Script",cursive;font-size:26px;color:#6f7378}
.hero-slogan{position:absolute;left:21px;top:240px;font-family:"Rubik",sans-serif;font-weight:700;font-size:25px;color:var(--navy)}
.hero-arrow{position:absolute;top:118px;width:56px;height:56px;border-radius:50%;border:2px solid #fff}
.hero-arrow.left{left:-34px}
.hero-arrow.right{left:560px}
.hero-arrow svg{position:absolute;top:19px}
.hero-arrow.left svg{left:38px}
.hero-arrow.right svg{left:6px}

/* main */
.main{top:419px;height:580px;background:var(--white)}
h2{font-family:"Ubuntu",sans-serif;font-weight:400;color:var(--navy)}
.welcome-title{position:absolute;left:24px;top:24px;font-size:15px}
.lead{position:absolute;left:24px;top:52px;width:330px;font-size:9.5px;line-height:15px;color:var(--orange)}
.body-text{position:absolute;left:24px;width:330px;font-size:6.6px;line-height:11px;color:var(--grey-text)}
.conditions-title{position:absolute;left:24px;top:180px;font-size:15px}
.cond-list{position:absolute;list-style:none;font-size:6.6px;color:var(--grey-text);line-height:17px}
.video-thumb{position:absolute;left:231px;top:206px;width:124px;height:76px;background:linear-gradient(135deg,#f1a44c 0%,#e4c7b3 50%,#f3f0ec 100%)}
.play{position:absolute;left:52px;top:28px;width:20px;height:20px;border-radius:50%;background:rgba(255,255,255,.7)}
.divider{position:absolute;left:24px;top:310px;width:331px;height:1px;background:#e3e3e3}

/* form */
.form-card{position:absolute;left:379px;top:3px;width:179px;height:307px;border:1px solid #e1e1e1;border-radius:6px 6px 4px 4px;background:#f9f9f9}
.form-title{position:absolute;left:0;width:100%;top:33px;text-align:center;font-family:"Ubuntu",sans-serif;font-size:12.5px;color:#555}
.form-title b{color:var(--orange);font-weight:700}
.form-sub{position:absolute;width:100%;top:52px;text-align:center;font-size:6.5px;font-style:italic;color:var(--navy)}
.field{position:absolute;left:9px;width:160px;height:21px;background:#fff;border:1px solid #e1e1e1;font-size:6.5px;font-style:italic;color:#999;padding:7px 6px}
.btn{position:absolute;height:24px;line-height:24px;text-align:center;color:#fff;font-size:7.5px;font-weight:700}
.form-phone{position:absolute;left:18px;top:283px;font-size:9px;font-weight:700;color:#777;display:flex;gap:5px;align-items:center}

/* features */
.feature{position:absolute;top:337px;width:100px;text-align:center}
.feature svg{display:block;margin:0 auto;height:36px}
.feature h3{font-family:"Ubuntu",sans-serif;font-weight:400;font-size:10px;color:var(--orange);margin-top:13px}
.feature p{font-size:6.4px;line-height:10.5px;color:#888;margin-top:10px}
.rule{position:absolute;left:0;top:463px;width:582px;height:1px;background:#ececec}
.fellow-title{position:absolute;width:100%;top:479px;text-align:center;font-family:"Ubuntu",sans-serif;font-size:13px;color:#555}
.fellow-title b{color:var(--orange);font-weight:700}
.fellow-sub{position:absolute;width:100%;top:503px;text-align:center;font-size:7px;color:#999}
.fellow-btn{position:absolute;left:230px;top:531px;width:122px;height:28px;line-height:28px;background:var(--orange);color:#fff;text-align:center;font-family:"Ubuntu",sans-serif;font-weight:700;font-size:10.5px}

/* locations */
.locations{top:999px;height:153px;background:#ededed}
.loc-title{position:absolute;left:25px;top:17px;font-size:12px}
.loc{position:absolute;top:41px;font-size:6.5px;line-height:13px;color:#666;white-space:nowrap}
.loc h4{font-family:"Ubuntu",sans-serif;font-weight:400;font-size:10px;color:var(--orange);margin-bottom:5px}
.loc .ph{font-size:9px;font-weight:700;color:var(--navy)}
.map{position:absolute;left:256px;top:44px;width:140px;height:72px;background:linear-gradient(180deg,#a9a9a9,#959595);border-radius:10px}
.news-title{position:absolute;left:411px;top:17px;font-size:12px}
.news-sub{position:absolute;left:411px;top:44px;font-size:7px;color:#666}
.news-sub span{color:var(--orange)}
.news-field{position:absolute;left:411px;top:62px;width:147px;height:26px;background:#fff;border:1px solid #ddd;font-size:7.5px;color:#666;padding:8px 7px}
.news-btn{position:absolute;left:466px;top:96px;width:91px;height:27px;line-height:27px;background:var(--orange);color:#fff;text-align:center;font-family:"Ubuntu",sans-serif;font-weight:700;font-size:10px}

/* footer */
.footer{position:absolute;left:0;top:1152px;width:682px;height:48px;background:var(--navy)}
.footer-nav{position:absolute;width:100%;top:11px;text-align:center;font-size:6.6px}
.footer-nav a{color:#fff;text-decoration:none;margin:0 3px}
.copyright{position:absolute;width:100%;top:29px;text-align:center;font-size:6px;color:#cfd8e4}
</style>
</head>
<body>

<header class="header">
  <div class="brand"><span class="brand-dot"></span><span class="brand-name">Mr Colin Brasket</span></div>
  <div class="contact-top">
    42 Seaview Parade,<br>PO BOX 7721, Geraldton WA 6530<br>
    <span class="phone">Ph: 08 9900 2157</span><br>Fax: 08 9900 2158
  </div>
  <div class="socials"><span></span><span></span><span></span><span></span><span></span></div>
</header>

<nav class="container nav">
  <a class="active" href="#">Home</a><a href="#">Appointments</a><a href="#">Surgical Fellowships</a><a href="#">Training Programs</a><a href="#">Memberships</a><a href="#">Publications</a><a href="#">Useful Websites</a><a href="#">Contact us</a>
</nav>

<div class="hero-band"></div>
<section class="container hero">
  <div class="hero-photo" role="img" aria-label="Photo of a podiatrist treating a patient's foot with a gloved hand and instrument"></div>
  <div class="hero-script">Podiatric Foot &amp; Ankle Surgeon</div>
  <div class="hero-slogan">Working hard to keep you on your feet.</div>
  <div class="hero-arrow left"><svg width="10" height="14" viewBox="0 0 10 14"><path d="M8 1 2 7l6 6" stroke="#fff" stroke-width="2.5" fill="none"/></svg></div>
  <div class="hero-arrow right"><svg width="10" height="14" viewBox="0 0 10 14"><path d="M2 1l6 6-6 6" stroke="#fff" stroke-width="2.5" fill="none"/></svg></div>
</section>

<main class="container main">
  <h2 class="welcome-title">Welcome to Our Site!!</h2>
  <p class="lead">The Stride Foot Care Group strive to provide exceptional service and care to all patients, young and old, to ensure they enjoy a pain free lifestyle.</p>
  <p class="body-text" style="top:98px">For those unfamiliar with our services, we are a team of accredited health professionals dealing with the prevention, diagnosis, treatment and rehabilitation of medical and surgical conditions related to feet, ankles and lower limbs.</p>
  <p class="body-text" style="top:142px">The Stride Foot Care Group have practices based throughout regional Western Australia in Geraldton and Kalgoorlie and offer the following services; sports injuries, foot care, foot orthoses and diabetes care.</p>

  <h2 class="conditions-title">Foot Conditions</h2>
  <ul class="cond-list" style="left:24px;top:202px"><li>Bunions</li><li>Tailors Bunion Deformity</li><li>Big Toe Joint Arthritis</li><li>Ganglions</li><li>Hammertoe Deformity</li></ul>
  <ul class="cond-list" style="left:138px;top:201px"><li>Hammertoe Deformity</li><li>Ingrown Toenails</li><li>Neuroma</li><li>Painful little toes</li></ul>
  <div class="video-thumb" role="img" aria-label="Video thumbnail of a foot treatment"><span class="play"></span></div>
  <div class="divider"></div>

  <form class="form-card">
    <div class="form-title">Request <b>FREE</b> Appointment</div>
    <div class="form-sub">Enter your details below and we will contact you</div>
    <div class="field" style="top:78px">Name:</div>
    <div class="field" style="top:105px">Email:</div>
    <div class="field" style="top:131px">Phone:</div>
    <div class="field" style="top:158px">Surgery:<svg width="8" height="5" style="position:absolute;right:6px;top:8px"><path d="M0 0h8L4 5z" fill="var(--navy)"/></svg></div>
    <div class="field" style="top:185px;height:47px">Message:</div>
    <div class="btn" style="left:11px;top:244px;width:71px;background:var(--orange)">SUBMIT FORM</div>
    <div class="btn" style="left:97px;top:244px;width:71px;background:var(--navy)">CONTACT US</div>
    <div class="form-phone"><svg width="14" height="14" viewBox="0 0 24 24"><path d="M6.6 10.8c1.4 2.8 3.8 5.1 6.6 6.6l2.2-2.2c.3-.3.7-.4 1-.2 1.1.4 2.3.6 3.6.6.6 0 1 .4 1 1V20c0 .6-.4 1-1 1C10.6 21 3 13.4 3 4c0-.6.4-1 1-1h3.5c.6 0 1 .4 1 1 0 1.3.2 2.5.6 3.6.1.3 0 .7-.2 1z" fill="var(--navy)"/></svg>08 9900 2157 , 08 9011 3864</div>
  </form>

  <div class="feature" style="left:26px">
    <svg viewBox="0 0 36 36" width="36"><path d="M8 27l2-7 14-14 5 5-14 14z" fill="var(--navy)"/><path d="M8 27l1-5 4 4z" fill="#fff"/></svg>
    <h3>Patient Forms</h3><p>Neque porro quisquam est dolorem ipsum quia dolor sit consectetur, adipisc.</p>
  </div>
  <div class="feature" style="left:133px">
    <svg viewBox="0 0 36 36" width="36"><path d="M3 2v32h32" stroke="var(--navy)" stroke-width="2" fill="none"/><rect x="7" y="14" width="4" height="18" fill="var(--navy)"/><rect x="13" y="19" width="4" height="13" fill="var(--navy)"/><rect x="19" y="23" width="4" height="9" fill="var(--navy)"/><rect x="25" y="27" width="4" height="5" fill="var(--navy)"/><path d="M6 8l26 22" stroke="var(--navy)" stroke-width="1.5"/></svg>
    <h3>Referral Forms</h3><p>Neque porro quisquam est dolorem ipsum quia dolor sit consectetur, adipisc.</p>
  </div>
  <div class="feature" style="left:238px">
    <svg viewBox="0 0 36 36" width="36"><ellipse cx="18" cy="10" rx="8" ry="6" fill="var(--navy)"/><ellipse cx="8" cy="22" rx="8" ry="6" fill="var(--navy)"/><ellipse cx="28" cy="22" rx="8" ry="6" fill="var(--navy)"/><path d="M18 15l-2 5 5-4zM8 27l-2 6 6-5zM28 27l2 6-6-5z" fill="var(--navy)"/></svg>
    <h3>Consulting</h3><p>Neque porro quisquam est dolorem ipsum quia dolor sit consectetur, adipisc.</p>
  </div>
  <div class="feature" style="left:346px">
    <svg viewBox="0 0 36 36" width="36"><circle cx="12" cy="10" r="6" fill="var(--navy)"/><path d="M2 32c0-9 4-14 10-14s10 5 10 14z" fill="var(--navy)"/><circle cx="25" cy="13" r="5" fill="var(--navy)"/><path d="M17 32c0-8 3-12 8-12s9 4 9 12z" fill="var(--navy)"/></svg>
    <h3>Memberships</h3><p>Neque porro quisquam est dolorem ipsum quia dolor sit consectetur, adipisc.</p>
  </div>
  <div class="feature" style="left:453px">
    <svg viewBox="0 0 36 36" width="36"><path d="M15 12c5 0 7 3 6 8-1 4-1 9-4 12-2 1-4 0-4-2 0-3 2-5 1-9-1-4-2-9 1-9z" fill="var(--navy)"/><circle cx="14" cy="6" r="3" fill="var(--navy)"/><circle cx="19" cy="5" r="2" fill="var(--navy)"/><circle cx="23" cy="7" r="1.7" fill="var(--navy)"/></svg>
    <h3>Fast Foot Facts</h3><p>Neque porro quisquam est dolorem ipsum quia dolor sit consectetur, adipisc.</p>
  </div>

  <div class="rule"></div>
  <h2 class="fellow-title">Surgical <b>FELLOWSHIPS</b> Trained</h2>
  <p class="fellow-sub">Lorem ipsum dolor sit amet, consectetur adipiscing elit. Donec quis tincidunt nisl.</p>
  <div class="fellow-btn">FIND OUT MORE</div>
</main>

<section class="container locations">
  <h2 class="loc-title">Our Locations</h2>
  <div class="loc" style="left:24px"><h4>Geraldton</h4>42 Seaview Parade,<br>PO BOX 7721,<br>Geraldton WA 6530<br><span class="ph">Ph: 08 9900 2157</span><br>Fax: 08 9900 2158</div>
  <div class="loc" style="left:166px"><h4>Kalgoorlie</h4>3/14 Harbour Lane,<br>Kalgoorlie WA 6430<br><span class="ph">Ph: 08 9011 3864</span><br>Fax: 08 9011 3865</div>
  <div class="map" role="img" aria-label="Grey world map with location pins"></div>
  <h2 class="news-title">Newsletter</h2>
  <p class="news-sub">Read our latest <span>newsletter.</span></p>
  <div class="news-field">Email:</div>
  <div class="news-btn">SUBSCRIBE</div>
</section>

<footer class="footer">
  <nav class="footer-nav"><a href="#">Home</a><a href="#">Appointments</a><a href="#">Surgical fellowships</a><a href="#">Training programs</a><a href="#">Memberships</a><a href="#">publications</a><a href="#">Useful websites</a><a href="#">Contact us</a></nav>
  <p class="copyright">© Copyright 2014 Colin Brasket all rights are reserved</p>
</footer>

</body>
</html>
```